KAJU Freightways #ALLKAJU Business Cards & Letterhead

I am looking to business cards designed for our organization. We are currently undergoing a small re-branding that is taking place. Our organization is called KAJU Freightways and we are headquartered in Phoenix, AZ. We primarily provide transportation and logistics services to the Marlow Parcel Bureau who is our largest customer. I would like to see a design that incorporates name, title, contact info, website, and address (this will be different depending on the employee). I would also like to see some color on the business card using our logo colors or a variation. I would like our logo on the back of the business card with the website displayed. The final design should communicate that we are a next generation transportation operate that focuses on being driver-first, customer-centric, innovative, and sustainable.We would also like our #ALLKAJU catch phrase incorporated as well.

Target Market(s)

Transportation & Logistics

Industry/Entity Type

Trucking Company

Contact Information for Business Card

-First and Last Name
-Position Title
-Contact Phone
-Contact Email
-Physical Address

Font styles to use
Serif

Colors

Designer to choose colors to be used in the design.

Requirements
Must have
• -KAJU logo prominently displayed
• -#ALLKAJU catch phrase used
• -Some amount of color, design gradient, etc.
• -Logo on the back with website listed (https://www.kajufreightco.example)

```html
<!DOCTYPE html>
<html lang="en">
<head>
<meta charset="utf-8">
<title>KAJU Freightways Business Card</title>
<link rel="stylesheet" href="https://fonts.googleapis.com/css2?family=Lora:wght@400;600;700&display=swap">
<style>
  :root {
    --teal-deep: #0f4756;
    --teal-mid: #1f6676;
    --teal-light: #3b8493;
    --lime: #8cc63f;
    --lime-soft: #a8d65f;
    --paper: #ffffff;
    --backdrop: #e9ebea;
    --ink-light: #eef4f5;
  }
  html, body {
    margin: 0;
    padding: 0;
    width: 1200px;
    height: 1023px;
    overflow: hidden;
    background: var(--backdrop);
  }
  .canvas {
    position: relative;
    width: 1200px;
    height: 1023px;
  }
  .card {
    position: absolute;
    left: 250px;
    width: 700px;
    height: 400px;
    border-radius: 18px;
    box-shadow: 0 10px 28px rgba(0, 0, 0, 0.18);
    overflow: hidden;
  }
  .card--front { top: 70px; }
  .card--back { top: 550px; }
  .card svg { display: block; }
  .card text {
    font-family: "Lora", serif;
  }
  .name { fill: var(--lime); font-weight: 600; font-size: 26px; letter-spacing: 0.5px; }
  .role { fill: var(--ink-light); font-weight: 400; font-size: 18px; }
  .detail { fill: var(--ink-light); font-weight: 400; font-size: 16px; }
  .web-accent { fill: var(--lime); }
  .icon { fill: none; stroke: var(--lime); stroke-width: 1.6; }
  .icon-solid { fill: var(--lime); }
  .wordmark { fill: var(--teal-deep); font-weight: 700; letter-spacing: 2px; }
  .tagline { fill: var(--lime); font-weight: 600; font-size: 20px; letter-spacing: 2px; }
  .back-web { fill: var(--teal-deep); font-weight: 400; font-size: 18px; letter-spacing: 0.5px; }
</style>
</head>
<body>
<main class="canvas">

  <section class="card card--front" aria-label="Business card front">
    <svg width="700" height="400" viewBox="0 0 700 400">
      <defs>
        <linearGradient id="tealPanel" x1="0" y1="0" x2="1" y2="1">
          <stop offset="0" stop-color="#0f4756"/>
          <stop offset="0.55" stop-color="#3b8493"/>
          <stop offset="1" stop-color="#0f4756"/>
        </linearGradient>
      </defs>
      <rect class="panel" width="700" height="400" fill="url(#tealPanel)"/>
      <rect class="white-field" x="500" y="0" width="200" height="400" fill="#ffffff"/>
      <circle class="badge-fill" cx="500" cy="200" r="205" fill="#ffffff"/>
      <circle class="badge-ring" cx="500" cy="200" r="180" fill="none" stroke="#a8d65f" stroke-width="7"/>
      <text class="wordmark" x="500" y="232" font-size="92" text-anchor="middle">KAJU</text>

      <rect class="edge-accent" x="0" y="44" width="8" height="34" fill="#8cc63f"/>
      <text class="name" x="30" y="70">DORIAN VALE</text>
      <text class="role" x="30" y="98">Director</text>

      <text class="detail" x="30" y="160">4410 North Cactus</text>
      <text class="detail" x="30" y="184">Ridge Road</text>
      <text class="detail" x="30" y="208">Glendale, AZ 85301</text>

      <path class="icon-solid" d="M32 262c2-3 5-3 6 0l-2 3c1 3 3 5 6 6l3-2c3 1 3 4 0 6-7 2-15-6-13-13z"/>
      <text class="detail" x="54" y="274">602-555-0148</text>

      <rect class="icon" x="31" y="293" width="14" height="10" rx="1"/>
      <path class="icon" d="M31 294l7 5 7-5"/>
      <text class="detail" x="54" y="304">info@kajufreightco.example</text>

      <circle class="icon" cx="38" cy="328" r="7"/>
      <path class="icon" d="M31 328h14M38 321c-4 4-4 10 0 14M38 321c4 4 4 10 0 14"/>
      <text class="detail" x="54" y="334">www.<tspan class="web-accent">kajufreightco</tspan>.example</text>
    </svg>
  </section>

  <section class="card card--back" aria-label="Business card back">
    <svg width="700" height="400" viewBox="0 0 700 400">
      <rect width="700" height="400" fill="#ffffff"/>
      <circle class="badge-ring" cx="350" cy="180" r="150" fill="none" stroke="#a8d65f" stroke-width="7"/>
      <text class="wordmark" x="350" y="206" font-size="84" text-anchor="middle">KAJU</text>
      <text class="tagline" x="350" y="250" text-anchor="middle">#ALLKAJU</text>
      <text class="back-web" x="350" y="372" text-anchor="middle">www.kajufreightco.example</text>
    </svg>
  </section>

</main>
</body>
</html>
```